Counselling practice needs a Business Card Design

I need a business card design for a new counselling practice in Canberra, Australia. The name of the practice is Dr Neil Hartwood, Counselling Services and the practice focuses on philosophical, narrative and existential counselling for individuals, couples and families. The final design should communicate professionalism, sophistication of analysis and psychological wholeness. The reverse side of the card should have an appointment reminder
Updates

Could the following qualifications also be included on card. BSc (Psychology), BA hons (Philosophy), PhD (Philosophy), Diploma of Community Counselling And the following affiliation Guidance and Wellbeing Society of Tarrin and Districts Inc. (GAWSOT) And my contact phone mobile phone number is 0478315942, and email is drneilhartwood@tarringuidance.example for inclusion as well.

Thank you all who have put in a design so far. I just wanted to clarify some design points based on what you have submitted. 1. The Guidance and Wellbeing Society. Tarrin and Districts Inc. (GAWSOT) is an affiliation only. 'Member of the Guidance and Wellbeing Society. Tarrin and Districts Inc (GAWSOT)' should appear with the same prominence of a qualification. 2. The Post Graduate Diploma in Community Counselling is a quaification and should appear as 'PG Dip (Community Counselling)' after the other qualifications. 3. I am advertising myself as a counsellor so 'Dr Neil Hartwood, Counselling Services' or 'Dr Neil Hartwood, Counsellor' is the equivalent of the business name. After looking at some of the designs I prefer Dr Neil Hartwood in sentence case rather than all capitals (DR NEIL HARTWOOD). 4. 'Philosophical, narrative and existential counselling for individuals, couples and families' is the description of the type of counselling services and should appear on the card.

One further point. I have updated my email address for the card. It is now drneilhartwood@tarringuidance.example

```html
<!DOCTYPE html>
<html lang="en">
<head>
<meta charset="utf-8">
<title>Dr Neil Hartwood – Counselling Services Business Card</title>
<link rel="stylesheet" href="https://fonts.googleapis.com/css2?family=Tinos&family=Arimo:wght@400&display=swap">
<style>
  :root {
    --stage: #e8eae5;
    --paper: #fbfbf9;
    --green-deep: #5fbf3f;
    --green-mid: #78cf55;
    --green-light: #94dc6c;
    --ink: #1b1b1b;
    --ink-soft: #3a3a3a;
    --on-green: #ffffff;
    --rule-on-green: rgba(255,255,255,0.85);
  }
  * { margin: 0; padding: 0; box-sizing: border-box; }
  html, body {
    width: 1200px; height: 858px; overflow: hidden;
    background: var(--stage);
  }
  .stage {
    width: 1200px; height: 858px;
    display: flex; flex-direction: column; align-items: center; justify-content: center;
    gap: 26px;
  }
  .card {
    width: 700px; height: 390px;
    position: relative; overflow: hidden;
    box-shadow: 0 6px 18px rgba(0,0,0,0.18);
  }
  .green-field {
    background: linear-gradient(160deg, var(--green-deep) 0%, var(--green-light) 55%, var(--green-mid) 100%);
  }

  /* Front */
  .card--front { display: flex; }
  .front__brand {
    width: 40%; background: var(--paper);
    display: flex; flex-direction: column; align-items: center; justify-content: center;
    text-align: center; padding: 0 24px; color: var(--ink);
  }
  .brand__name {
    font-family: "Tinos", "Times New Roman", serif;
    font-size: 34px; line-height: 1.1;
  }
  .brand__role {
    font-family: "Arimo", Arial, sans-serif;
    font-size: 17px; margin-top: 10px;
  }
  .brand__services {
    font-family: "Arimo", Arial, sans-serif;
    font-size: 12.5px; line-height: 1.45; color: var(--ink-soft);
    margin-top: 18px;
  }
  .front__details {
    flex: 1; position: relative; color: var(--on-green);
    font-family: "Arimo", Arial, sans-serif;
  }
  .credentials {
    position: absolute; top: 34px; right: 32px; text-align: right;
  }
  .credentials__list { list-style: none; font-size: 14px; line-height: 1.6; }
  .credentials__member { margin-top: 10px; font-size: 13px; line-height: 1.45; }
  .contact {
    position: absolute; left: 30px; bottom: 34px;
    list-style: none; font-size: 14px; line-height: 1.8;
  }
  .contact__item { display: flex; align-items: center; gap: 10px; }
  .contact__icon { width: 11px; height: 11px; flex: none; }

  /* Back */
  .card--back {
    display: flex; flex-direction: column; align-items: center; justify-content: center;
    color: var(--on-green);
  }
  .reminder__title {
    font-family: "Tinos", "Times New Roman", serif;
    font-size: 44px; line-height: 1;
  }
  .reminder__with {
    font-family: "Arimo", Arial, sans-serif;
    font-size: 16px; margin-top: 12px;
  }
  .reminder__fields {
    list-style: none; margin-top: 34px; width: 460px;
    font-family: "Arimo", Arial, sans-serif; font-size: 16px;
  }
  .reminder__field {
    display: flex; align-items: flex-end; gap: 14px; height: 40px;
  }
  .reminder__label { width: 52px; flex: none; }
  .reminder__line { flex: 1; border-bottom: 1px solid var(--rule-on-green); height: 1px; margin-bottom: 4px; }
  .reminder__note {
    font-family: "Arimo", Arial, sans-serif;
    font-size: 13px; margin-top: 26px;
  }
</style>
</head>
<body>
<main class="stage">
  <section class="card card--front" aria-label="Card front">
    <div class="front__brand">
      <div class="brand__name">Dr Neil Hartwood</div>
      <div class="brand__role">Counselling Services</div>
      <p class="brand__services">Philosophical, narrative and existential<br>counselling for individuals,<br>couples and families</p>
    </div>
    <div class="front__details green-field">
      <div class="credentials">
        <ul class="credentials__list">
          <li>BSc (Psychology)</li>
          <li>BA hons (Philosophy)</li>
          <li>PhD (Philosophy)</li>
          <li>PG Dip (Community Counselling)</li>
        </ul>
        <p class="credentials__member">Member of the Guidance and Wellbeing Society.<br>Tarrin and Districts Inc (GAWSOT)</p>
      </div>
      <ul class="contact">
        <li class="contact__item">
          <svg class="contact__icon" viewBox="0 0 11 11" aria-hidden="true"><rect x="2.5" y="0.5" width="6" height="10" rx="1" fill="none" stroke="#fff"/><rect x="4.5" y="8" width="2" height="1" fill="#fff"/></svg>
          <span>0478315942</span>
        </li>
        <li class="contact__item">
          <svg class="contact__icon" viewBox="0 0 11 11" aria-hidden="true"><rect x="0.5" y="2" width="10" height="7" fill="none" stroke="#fff"/><path d="M0.5 2 L5.5 6 L10.5 2" fill="none" stroke="#fff"/></svg>
          <span>drneilhartwood@tarringuidance.example</span>
        </li>
      </ul>
    </div>
  </section>

  <section class="card card--back green-field" aria-label="Card back">
    <div class="reminder__title">Appointment Reminder</div>
    <div class="reminder__with">Dr Neil Hartwood, Counsellor</div>
    <ul class="reminder__fields">
      <li class="reminder__field"><span class="reminder__label">Name</span><span class="reminder__line"></span></li>
      <li class="reminder__field"><span class="reminder__label">Date</span><span class="reminder__line"></span></li>
      <li class="reminder__field"><span class="reminder__label">Time</span><span class="reminder__line"></span></li>
    </ul>
    <p class="reminder__note">Please give 24 hours notice if you cannot attend &nbsp;·&nbsp; 0478315942</p>
  </section>
</main>
</body>
</html>
```